Los Brava Dip – CPG Website with WordPress - Store Locator: WP Maps plugin

Larkfield Food Company is a startup consumer packaged goods (CPG) brand launching its flagship product line — Los Brava Dip. We’re seeking a talented web designer to create a bold, professional, mobile-optimized website using WordPress with a WP Maps store locator to help customers find local retailers.

Our goal is to build a strong online presence that supports both retail growth and direct-to-consumer sales.

See Los Brava _Website_Design_Brief word document.

The website URL is https://losbravadip.example/

Target Market(s)

Consumers of gourmet salsa

Industry/Entity Type

Consumer Packaged Goods - Salsa manufacturer.

Coding

Coded - Design and coding required

Number of Pages Required

5+ page

Requirements
Must have
• The design of the Los Brava Dip website shall emulate the clean, polished aesthetic of Fennigo.example.

```html
<!DOCTYPE html>
<html lang="en">
<head>
<meta charset="utf-8">
<title>Los Brava Dip</title>
<link rel="stylesheet" href="https://fonts.googleapis.com/css2?family=Montserrat:wght@400;500;600;700;800&family=Poppins:wght@400;500;600&display=swap">
<style>
:root{
  --red:#c8321e;
  --red-dark:#a8261a;
  --orange:#e3612a;
  --green:#2f5d1f;
  --yellow:#f3c13a;
  --ink:#1d1d1d;
  --muted:#666;
  --line:#c8321e;
  --white:#fff;
  --gold:#e19a1c;
  --star:#1f9d55;
}
*{box-sizing:border-box;margin:0;padding:0}
html,body{width:1200px;height:3184px;overflow:hidden}
body{font-family:"Montserrat",sans-serif;color:var(--ink);background:var(--white);position:relative}
.site-header{height:60px;display:flex;align-items:center;padding:0 100px;position:relative;background:var(--white)}
.nav{display:flex;gap:48px;font-size:13px;font-weight:600;letter-spacing:.5px}
.nav a{color:var(--ink);text-decoration:none}
.nav-right{margin-left:auto;align-items:center}
.brand{position:absolute;left:50%;transform:translateX(-50%);top:8px;font-weight:800;font-size:26px;color:var(--red);white-space:nowrap}
.btn-contact{background:var(--red);color:#fff!important;padding:8px 20px;font-size:12px}
.hero{height:660px;background:radial-gradient(ellipse at 50% 80%,#f08a3a 0%,var(--orange) 40%,var(--red) 100%);text-align:center;position:relative;color:#fff}
.hero h1{padding-top:52px;font-size:52px;font-weight:700;line-height:1.15;letter-spacing:1px}
.hero h1 span{display:inline-block;border-bottom:2px solid rgba(255,255,255,.6);padding:0 30px 6px}
.btn-outline{display:inline-block;border:2px solid #fff;color:#fff;font-size:13px;font-weight:600;padding:10px 26px;margin-top:26px;letter-spacing:.5px}
.hero-jars{position:absolute;left:360px;top:320px;width:480px;height:340px;border-radius:20px;background:linear-gradient(90deg,#d46a26,#a9c24a 50%,#d6452c)}
.section-title{text-align:center;font-size:34px;font-weight:600;letter-spacing:1px;position:relative}
.section-title:before,.section-title:after{content:"";position:absolute;left:100px;right:100px;height:1px;background:currentColor;opacity:.6}
.section-title:before{top:-12px}.section-title:after{bottom:-12px}
.featured{height:720px;padding-top:78px}
.featured .section-title{color:var(--ink)}
.featured .section-title:before,.featured .section-title:after{background:var(--line);opacity:.8}
.cards{display:flex;gap:20px;justify-content:center;margin-top:90px}
.product{width:320px;height:440px;border:1px solid #ddd;box-shadow:0 4px 14px rgba(0,0,0,.12);text-align:center;padding:30px 20px;background:#fff}
.product .jar{width:120px;height:180px;margin:0 auto;border-radius:14px}
.product .tag{margin-top:22px;font-size:13px;font-weight:700;letter-spacing:1.5px}
.product h3{font-size:30px;font-weight:600;letter-spacing:3px}
.product p{font-size:12px;color:var(--muted);margin-top:8px;line-height:1.5;font-family:"Poppins",sans-serif}
.btn-line{display:inline-block;border:1.5px solid var(--red);color:var(--ink);font-size:11px;font-weight:600;padding:8px 22px;margin-top:18px;letter-spacing:.5px}
.reviews{height:552px;background:var(--green);color:#fff;padding-top:84px}
.reviews .summary{text-align:center;font-size:20px;margin-top:64px;font-weight:500}
.reviews .summary small{font-size:14px}
.stars{color:#fff;letter-spacing:2px}
.review-row{display:flex;gap:20px;justify-content:center;margin-top:28px}
.review{width:320px;height:200px;background:#fff;color:var(--ink);padding:26px 24px}
.review .stars-box{display:flex;gap:3px}
.review .stars-box i{width:18px;height:18px;background:var(--star);display:block;position:relative}
.review .stars-box i:after{content:"★";color:#fff;font-size:13px;font-style:normal;position:absolute;left:3px;top:0}
.review h4{margin-top:14px;font-size:16px;font-weight:600}
.review p{font-size:12px;color:var(--muted);line-height:1.5;margin-top:8px;font-family:"Poppins",sans-serif}
.review .who{margin-top:16px;font-weight:600;font-size:14px}
.arrows{display:flex;justify-content:center;gap:26px;margin-top:30px}
.recipes{height:708px;background:var(--yellow);padding-top:92px}
.recipe-card{margin:98px 0 0 140px;width:960px;height:420px;background:#fff;box-shadow:0 6px 18px rgba(0,0,0,.15);display:flex;position:relative}
.recipe-photo{width:448px;height:420px;background:linear-gradient(135deg,#2c3f7a,#e0a253 55%,#3f7a2a)}
.recipe-body{padding:56px 40px 0 40px;width:512px}
.recipe-body h3{font-size:26px;font-weight:700;line-height:1.2;letter-spacing:.5px}
.recipe-body .rule{width:40px;height:3px;background:var(--gold);margin:12px 0 14px}
.recipe-body p{font-size:13.5px;color:#444;line-height:1.6;font-family:"Poppins",sans-serif}
.recipe-card .arrows{position:absolute;right:40px;bottom:40px;margin:0}
.instagram{height:120px;background:var(--red);color:#fff;display:flex;align-items:center;justify-content:center}
.instagram .section-title{font-size:30px;width:100%}
.site-footer{height:300px;display:flex;padding:60px 100px 0 110px;gap:0}
.foot-brand{width:290px}
.foot-brand .name{font-weight:800;font-size:30px;color:var(--red)}
.socials{display:flex;gap:14px;margin-top:12px}
.socials span{width:30px;height:30px;border-radius:50%;background:var(--red);display:block}
.socials span+span{background:none;border:2px solid var(--ink)}
.foot-col h5{font-size:18px;font-weight:700;border-bottom:2px solid var(--ink);padding-bottom:4px;display:inline-block;letter-spacing:.5px}
.foot-links{display:flex;gap:70px;margin-top:14px}
.foot-links ul{list-style:none;font-size:14px;line-height:1.75;font-family:"Poppins",sans-serif}
.foot-nav{width:400px}
.contact-line{display:flex;align-items:center;gap:10px;margin-top:18px;font-size:14px;font-family:"Poppins",sans-serif}
.copyright{height:64px;border-top:1px solid #ddd;text-align:center;font-size:12px;color:#555;padding-top:22px;font-family:"Poppins",sans-serif}
</style>
</head>
<body>
<header class="site-header">
  <nav class="nav"><a>ABOUT</a><a>PRODUCTS</a><a>WHERE TO BUY</a></nav>
  <div class="brand">Los Brava</div>
  <nav class="nav nav-right"><a>RECIPES</a><a>REVIEW</a><a class="btn-contact">CONTACT ›</a></nav>
</header>

<section class="hero">
  <h1><span>SPICE UP YOUR MEALS!</span><br>WITH LOS BRAVA</h1>
  <a class="btn-outline">SHOP NOW ›</a>
  <div class="hero-jars" role="img" aria-label="Three jars of Los Brava habanero, verde and all natural salsa"></div>
</section>

<section class="featured">
  <h2 class="section-title">FEATURED PRODUCT</h2>
  <div class="cards">
    <article class="product">
      <div class="jar" role="img" aria-label="Jar of all natural salsa" style="background:linear-gradient(#c84a24,#e07a2f)"></div>
      <div class="tag" style="color:var(--gold)">ALL NATURAL</div>
      <h3>SALSA</h3>
      <p>Fresh tomatoes, onion and chile, slow blended<br>for a bright everyday bite.</p>
      <a class="btn-line">VIEW DETAIL</a>
    </article>
    <article class="product">
      <div class="jar" role="img" aria-label="Jar of habanero salsa" style="background:linear-gradient(#b82a1c,#d8482a)"></div>
      <div class="tag" style="color:var(--red)">HABANERO</div>
      <h3>SALSA</h3>
      <p>Roasted habanero heat balanced with sweet<br>tomato and a squeeze of lime.</p>
      <a class="btn-line">VIEW DETAIL</a>
    </article>
    <article class="product">
      <div class="jar" role="img" aria-label="Jar of verde salsa" style="background:linear-gradient(#6f9a2e,#a9c24a)"></div>
      <div class="tag" style="color:var(--green)">VERDE</div>
      <h3>SALSA</h3>
      <p>Tangy tomatillo, jalapeño and cilantro<br>for a crisp green finish.</p>
      <a class="btn-line">VIEW DETAIL</a>
    </article>
  </div>
</section>

<section class="reviews">
  <h2 class="section-title">REVIEWS</h2>
  <div class="summary">Let Customer Speak for us <span class="stars">★★★★★</span> <small>from 448 reviews</small></div>
  <div class="review-row">
    <article class="review"><div class="stars-box"><i></i><i></i><i></i><i></i><i></i></div><h4>Awesome taste, fresh</h4><p>Bright and fresh with just the right kick, we finish a jar every weekend.</p><div class="who">Dana Reyes</div></article>
    <article class="review"><div class="stars-box"><i></i><i></i><i></i><i></i><i></i></div><h4>Awesome taste, fresh</h4><p>Bright and fresh with just the right kick, we finish a jar every weekend.</p><div class="who">Dana Reyes</div></article>
    <article class="review"><div class="stars-box"><i></i><i></i><i></i><i></i><i></i></div><h4>Awesome taste, fresh</h4><p>Bright and fresh with just the right kick, we finish a jar every weekend.</p><div class="who">Dana Reyes</div></article>
  </div>
  <div class="arrows">
    <svg width="14" height="24" viewBox="0 0 14 24"><path d="M12 2 2 12l10 10" fill="none" stroke="#fff" stroke-width="2.5"/></svg>
    <svg width="14" height="24" viewBox="0 0 14 24"><path d="M2 2l10 10L2 22" fill="none" stroke="#fff" stroke-width="2.5"/></svg>
  </div>
</section>

<section class="recipes">
  <h2 class="section-title">RECIPES</h2>
  <article class="recipe-card">
    <div class="recipe-photo" role="img" aria-label="Plate of baked chicken topped with salsa and sour cream with greens"></div>
    <div class="recipe-body">
      <h3>BAKED CHICKEN WITH<br>SALSA AND SOUR CREAM</h3>
      <div class="rule"></div>
      <p>Looking for a weeknight dinner that’s both effortless and packed with flavor? This Baked Chicken with Salsa and Sour Cream is a creamy, cheesy, oven-baked comfort dish that’s as satisfying as it is simple. Seasoned with taco spices</p>
      <a class="btn-line">VIEW RECIPE</a>
    </div>
    <div class="arrows">
      <svg width="12" height="22" viewBox="0 0 14 24"><path d="M12 2 2 12l10 10" fill="none" stroke="#999" stroke-width="2.5"/></svg>
      <svg width="12" height="22" viewBox="0 0 14 24"><path d="M2 2l10 10L2 22" fill="none" stroke="#999" stroke-width="2.5"/></svg>
    </div>
  </article>
</section>

<section class="instagram">
  <h2 class="section-title">FOLLOW US ON INSTAGRAM</h2>
</section>

<footer class="site-footer">
  <div class="foot-brand">
    <div class="name">Los Brava</div>
    <div class="socials"><span></span><span></span></div>
  </div>
  <div class="foot-col foot-nav">
    <h5>NAVIGATION</h5>
    <div class="foot-links">
      <ul><li>About Us</li><li>Products</li><li>Recipes</li><li>Reviews</li></ul>
      <ul><li>Privacy Policy</li><li>Shipping Policy</li><li>Terms and Conditions</li><li>Contact us</li></ul>
    </div>
  </div>
  <div class="foot-col">
    <h5>CONTACT US</h5>
    <div class="contact-line">
      <svg width="26" height="26" viewBox="0 0 26 26"><circle cx="13" cy="13" r="13" fill="#1d1d1d"/><rect x="6.5" y="8.5" width="13" height="9" fill="none" stroke="#fff" stroke-width="1.5"/><path d="M6.5 8.5 13 14l6.5-5.5" fill="none" stroke="#fff" stroke-width="1.5"/></svg>
      support@losbravadip.example
    </div>
  </div>
</footer>
<div class="copyright">Copyright © 2025 Brightmoor Studio . All Right Reserved</div>
</body>
</html>
```